Private Investigation Business Card Design

I need a business card for a new private investigation company named Brisk Inquiries. I perform mainly surveillance jobs, vehicle repossessions, document serves etc. The final design should aim for a professional look. The logo has a magnifying glass with stick man arms and legs and is in a running action to show the "Brisk" aspect of the name. If the colour scheme could remain the same as the website www.briskinquiries-demo.com.au with silvers,blacks and a couple electric blue highlights.
Industry/Entity Type
Business
Contact Information for Business Card
Morgan Kellaway
Brisk Inquiries
0487316204
PO Box 58, Carnwell NSW 2291
info@briskinquiries-demo.com.au
www.briskinquiries-demo.com.au
Look and feel

```html
<!DOCTYPE html>
<html lang="en">
<head>
<meta charset="utf-8">
<title>Brisk Inquiries – Business Card</title>
<link rel="stylesheet" href="https://fonts.googleapis.com/css2?family=Michroma&family=Questrial&display=swap">
<style>
  :root {
    --backdrop: #2b2b2b;
    --card-dark: #1f1f1f;
    --card-light: #f4f5f6;
    --silver: #a9acb0;
    --band: #222222;
    --electric-blue: #5b9be0;
    --text-dark: #202020;
  }
  * { box-sizing: border-box; margin: 0; padding: 0; }
  html, body { width: 1200px; height: 900px; overflow: hidden; }
  body {
    background: var(--backdrop);
    font-family: "Questrial", "Helvetica Neue", Arial, sans-serif;
    position: relative;
  }

  .card {
    position: absolute;
    width: 620px;
    height: 376px;
    border-radius: 4px;
    overflow: hidden;
    box-shadow: 0 18px 40px rgba(0,0,0,0.55);
  }

  /* Front card */
  .card--front {
    left: 80px;
    top: 60px;
    background: linear-gradient(160deg, #2a2a2a 0%, var(--card-dark) 60%, #151515 100%);
  }
  .card--front .brand {
    position: absolute;
    left: 50px;
    top: 56px;
    z-index: 1;
  }
  .brand__name {
    font-family: "Michroma", "Arial Black", sans-serif;
    color: var(--silver);
    font-size: 46px;
    line-height: 1;
    letter-spacing: 2px;
    text-transform: uppercase;
  }
  .brand__sub {
    font-family: "Michroma", "Arial Black", sans-serif;
    color: var(--silver);
    font-size: 13px;
    letter-spacing: 5px;
    margin-top: 8px;
    text-transform: uppercase;
  }
  .front-illustration {
    position: absolute;
    left: 120px;
    top: 140px;
    width: 460px;
    height: 200px;
    border-radius: 6px;
    background: linear-gradient(90deg, #262626 0%, #3a3a3a 55%, #555555 100%);
  }

  /* Back card */
  .card--back {
    left: 500px;
    top: 480px;
    background: linear-gradient(135deg, #ffffff 0%, var(--card-light) 60%, #e7e8ea 100%);
  }
  .card--back .brand {
    position: absolute;
    left: 70px;
    top: 34px;
  }
  .card--back .brand__name { font-size: 38px; }
  .card--back .brand__sub { font-size: 11px; letter-spacing: 4px; }
  .runner-mini {
    position: absolute;
    left: 350px;
    top: 52px;
    width: 60px;
    height: 54px;
    border-radius: 6px;
    background: #dcdddf;
  }
  .name-band {
    position: absolute;
    left: 0;
    right: 0;
    top: 126px;
    height: 58px;
    background: var(--band);
    border-top: 3px solid var(--electric-blue);
    border-bottom: 3px solid var(--electric-blue);
  }
  .name-band::after {
    content: "";
    position: absolute;
    left: 40px;
    bottom: -13px;
    border-left: 10px solid transparent;
    border-right: 10px solid transparent;
    border-top: 10px solid var(--band);
  }
  .name-band__name {
    position: absolute;
    left: 40px;
    top: 14px;
    font-family: "Michroma", "Arial Black", sans-serif;
    color: #ffffff;
    font-size: 22px;
    letter-spacing: 2px;
    white-space: nowrap;
  }
  .contact-list {
    position: absolute;
    left: 40px;
    top: 208px;
    list-style: none;
  }
  .contact-list__item {
    display: flex;
    align-items: center;
    gap: 12px;
    font-size: 19px;
    color: var(--text-dark);
    line-height: 1;
    margin-bottom: 12px;
    white-space: nowrap;
  }
  .contact-list__item svg { width: 16px; height: 16px; flex: none; }
  .runner-watermark-art {
    position: absolute;
    right: 20px;
    bottom: 12px;
    width: 190px;
    height: 160px;
    border-radius: 8px;
    background: radial-gradient(ellipse at 50% 50%, rgba(205,206,208,0.45), rgba(240,240,240,0) 70%);
  }
</style>
</head>
<body>

<section class="card card--front" aria-label="Card front">
  <div class="front-illustration" role="img" aria-label="Illustration: running magnifying-glass figure heading towards a lit open doorway"></div>
  <div class="brand">
    <div class="brand__name">Brisk</div>
    <div class="brand__sub">Inquiries</div>
  </div>
</section>

<section class="card card--back" aria-label="Card back">
  <div class="runner-watermark-art" role="img" aria-label="Faint large running magnifying-glass figure"></div>
  <div class="brand">
    <div class="brand__name">Brisk</div>
    <div class="brand__sub">Inquiries</div>
  </div>
  <div class="runner-mini" role="img" aria-label="Small running magnifying-glass figure"></div>

  <div class="name-band">
    <div class="name-band__name">MORGAN KELLAWAY</div>
  </div>

  <ul class="contact-list">
    <li class="contact-list__item">
      <svg viewBox="0 0 16 16" aria-hidden="true"><path d="M4 1.5l2.2 3-1.3 1.5c.8 1.8 2.3 3.3 4.1 4.1l1.5-1.3 3 2.2-1.2 2.5C7 13 3 9 1.5 2.7z" fill="var(--electric-blue)"/></svg>
      <span>0487316204</span>
    </li>
    <li class="contact-list__item">
      <svg viewBox="0 0 16 16" aria-hidden="true"><path d="M8 1a5 5 0 0 0-5 5c0 3.6 5 9 5 9s5-5.4 5-9a5 5 0 0 0-5-5zm0 7a2 2 0 1 1 0-4 2 2 0 0 1 0 4z" fill="var(--electric-blue)"/></svg>
      <span>PO Box 58, Carnwell NSW 2291</span>
    </li>
    <li class="contact-list__item">
      <svg viewBox="0 0 16 16" aria-hidden="true"><rect x="1" y="3" width="14" height="10" rx="1" fill="var(--electric-blue)"/><path d="M1.5 3.8L8 9l6.5-5.2" stroke="#fff" stroke-width="1.3" fill="none"/></svg>
      <span>info@briskinquiries-demo.com.au</span>
    </li>
    <li class="contact-list__item">
      <svg viewBox="0 0 16 16" aria-hidden="true"><circle cx="8" cy="8" r="6.5" fill="none" stroke="var(--electric-blue)" stroke-width="1.5"/><path d="M1.5 8h13M8 1.5c-3 3.5-3 9.5 0 13M8 1.5c3 3.5 3 9.5 0 13" fill="none" stroke="var(--electric-blue)" stroke-width="1.2"/></svg>
      <span>www.briskinquiries-demo.com.au</span>
    </li>
  </ul>
</section>

</body>
</html>
```